Online class need a Chapter Template

Basically, I have two main document templates:

Template 1: Chapter unit or the abstract concept explanation.

There are 4 main chapters and each chapter is linked to a color:
(RED Color) : Learning Communities
(YELLOW Color): Exploring Online Learning Tools
(BLUE Color): Teaching and Learning Fundamentals
(GREEN Color): Online Teaching and Learning in Practice

Inside the chapter there are the same elements:
Learning Objectives
Introduction
Context
Concept Explanation
Activities (directions, challenge or task to perform)

Template 2: The tool guide and practical skill requirement

This one describes how to use an online tool
Updates

Good day everyone, I added a new file with the current template. I am using PageLoomMaker and really want to make this a little easier.

The project is about the Layout design of the Unit / Activity, and the layout proposal can be done in any tool

I really hope the new file helps explaining the concept (Sorry, English is not my primary language, but I will try my best)

Reason: Hi everyone, I am extending the deadline by 5 days to give the opportunity to the new invitees to submit their designs. I am looking forward to see your ideas! Kind regards, Tobias

Reason: Changed the project type in order to make it easier for designers to participate. Looking forward to your designs. Kind regards.

Reason: Waiting for a couple of designs re-submissions

Target Market(s)

The audience are online students 16-25 years old

Industry/Entity Type

Learning

Requirements
Must have
• For the Template 1 (Chapter) (see old sample attached)
The following elements are needed (each one with a graphic icon):
Learning Objectives
Introduction
Context
Concept Explanation

For the Template 2 (Tool) (see old sample attached)
Any creative idea is open here. This is basically the template to a small tutorial. The elements are:
Tool name and description
Where to find it (It contains the URL and QR Code)
Checklist template
Explanation Links
Tool Screenshots
Nice to have
• I am open to ideas. At the end, the main result will be five editable templates
4 chapter templates (sample named template 1) (RED, YELLOW, BLUE and GREEN)
1 Tool template (sample named template 2)

```html
<!DOCTYPE html>
<html lang="es">
<head>
<meta charset="UTF-8">
<title>Comunidades Virtuales de Aprendizaje – Actividad 02</title>
<link href="https://fonts.googleapis.com/css2?family=Raleway:wght@300;400&family=Lora:ital,wght@1,400&display=swap" rel="stylesheet">
<style>
  :root {
    --chapter-green: #3cb54a;
    --panel-grey: #efefef;
    --badge-grey: #c8c8c8;
    --ring-grey: #c4c4c4;
    --media-grey: #ececec;
    --ink: #333333;
    --white: #ffffff;
  }
  * { margin: 0; padding: 0; box-sizing: border-box; }
  html, body { width: 849px; height: 1200px; overflow: hidden; background: var(--white); }
  .page { position: relative; width: 849px; height: 1200px; background: var(--white); }

  .chapter-header { position: absolute; top: 0; left: 0; width: 849px; height: 222px; display: flex; }
  .chapter-title {
    width: 660px; height: 100%; background: var(--chapter-green);
    color: var(--white); font-family: "Raleway", sans-serif; font-weight: 300;
    font-size: 48px; line-height: 1.22; padding: 34px 0 0 28px; letter-spacing: 0.5px;
  }
  .chapter-number {
    flex: 1; background: var(--panel-grey); color: var(--chapter-green);
    font-family: "Raleway", sans-serif; font-weight: 300; font-size: 104px;
    display: flex; justify-content: center; padding-top: 20px; line-height: 1;
  }

  .activity-badge {
    position: absolute; left: 51px; top: 268px; width: 174px; height: 174px;
    border-radius: 50%; background: var(--badge-grey);
    display: flex; flex-direction: column; align-items: center; justify-content: center;
    font-family: "Lora", serif; font-style: italic; color: var(--ink);
    font-size: 32px; line-height: 1.15;
  }
  .duration-ring { position: absolute; left: 244px; top: 268px; width: 174px; height: 174px; }
  .duration-ring svg { position: absolute; inset: 0; }
  .duration-label {
    position: absolute; inset: 0; display: flex; flex-direction: column;
    align-items: center; justify-content: center;
    font-family: "Lora", serif; font-style: italic; color: var(--chapter-green);
    font-size: 28px; line-height: 1.15;
  }

  .activity-media {
    position: absolute; left: 28px; top: 467px; width: 793px; height: 320px;
    background: var(--media-grey);
  }
  .activity-text {
    position: absolute; left: 28px; top: 800px; width: 793px;
    font-family: "Lora", serif; font-style: italic; font-size: 19.5px;
    line-height: 1.3; color: var(--ink); text-align: justify;
  }
  .activity-steps { position: absolute; left: 113px; top: 943px; list-style: none; }
  .activity-steps li {
    display: flex; align-items: center; height: 57px;
    font-family: "Lora", serif; font-style: italic; font-size: 20px; color: var(--ink);
  }
  .activity-steps li::before {
    content: ""; width: 28px; height: 28px; border-radius: 50%;
    background: var(--chapter-green); margin-right: 30px; flex-shrink: 0;
  }

  .chapter-footer { position: absolute; left: 0; top: 1127px; width: 849px; height: 46px; display: flex; }
  .footer-band { width: 660px; background: var(--chapter-green); }
  .footer-number {
    flex: 1; background: var(--panel-grey); color: var(--chapter-green);
    font-family: "Raleway", sans-serif; font-weight: 400; font-size: 30px;
    display: flex; align-items: center; justify-content: center;
  }
</style>
</head>
<body>
<div class="page">
  <header class="chapter-header">
    <h1 class="chapter-title">Comunidades Virtuales<br>de Aprendizaje</h1>
    <div class="chapter-number">01</div>
  </header>

  <div class="activity-badge"><span>activity</span><span>02</span></div>

  <div class="duration-ring">
    <svg viewBox="0 0 174 174" width="174" height="174" aria-hidden="true">
      <circle cx="87" cy="87" r="80" fill="none" stroke="var(--ring-grey)" stroke-width="10"
              stroke-dasharray="37.89 4" stroke-dashoffset="-2" transform="rotate(-90 87 87)"/>
      <circle cx="87" cy="87" r="80" fill="none" stroke="var(--chapter-green)" stroke-width="10"
              stroke-dasharray="37.89 4 37.89 4 37.89 4 37.89 4 37.89 4 37.89 255.31" stroke-dashoffset="-2" transform="rotate(-90 87 87)"/>
    </svg>
    <div class="duration-label"><span>30</span><span>minutes</span></div>
  </div>

  <div class="activity-media" role="img" aria-label="Imagen de la actividad"></div>

  <p class="activity-text">Lorem ipsum dolor sit amet, consectetur adipisicing elit, sed do eiusmod tempor incididunt ut labore et dolore magna aliqua. Ut enim ad minim veniam, quis nostrud exercitation ullamco laboris nisi ut aliquip ex ea commodo consequat. Duis aute</p>

  <ul class="activity-steps">
    <li>Lorem ipsum dolor sit amet, consectetur adipisicing elit, sed do</li>
    <li>Lorem ipsum dolor sit amet, consectetur</li>
  </ul>

  <footer class="chapter-footer">
    <div class="footer-band"></div>
    <div class="footer-number">01</div>
  </footer>
</div>
</body>
</html>
```